New business card/stationary for a consulting company

I am looking for a clean and very professional looking business card for my consulting company as well as corresponding stationary. I am uploading our logo. I like simple and powerful for the feel. No graphics but I am open on everything else. Below is my contact information but would like the final to be in a version I can add my employees information into and print. Thank you.

Daniel Whitcombe
dan@ferncliffadvisory.com
2870 North 9th Avenue, Summit Floor, Elm Ridge, Illinois 60531
www.ferncliffadvisory.com

Industry/Entity Type

Consulting

Contact Information for Business Card

Daniel Whitcombe
dan@ferncliffadvisory.com
www.ferncliffadvisory.com

Font styles to use
Serif
Sans Serif

Requirements
Must have
• Our logo and the business card details.
Nice to have
• our website www.ferncliffadvisory.com

```html
<!DOCTYPE html>
<html lang="en">
<head>
<meta charset="utf-8">
<title>Ferncliff Advisory — Business Card</title>
<link href="https://fonts.googleapis.com/css2?family=Roboto:wght@300;400&display=swap" rel="stylesheet">
<style>
  :root {
    --backdrop: #3a3a3c;
    --card-dark: #2b2b2d;
    --panel-dark: #333335;
    --brand-blue: #0e4479;
    --ink-light: #ffffff;
    --ink-muted: #8a8a8e;
  }
  * { margin: 0; padding: 0; box-sizing: border-box; }
  html, body {
    width: 799px; height: 1200px; overflow: hidden;
    background: var(--backdrop);
    font-family: "Roboto", Arial, sans-serif;
  }
  .card {
    position: absolute; left: 90px;
    width: 620px; height: 354px;
    box-shadow: 0 12px 30px rgba(0,0,0,0.45);
    overflow: hidden;
  }
  .card-front { top: 150px; background: var(--card-dark); }
  .card-back { top: 680px; background: var(--brand-blue); }

  .front-brand {
    position: absolute; left: 50%; top: 50%;
    transform: translate(-50%, -50%);
    display: flex; align-items: center; gap: 16px;
  }
  .front-brand .mark {
    width: 22px; height: 22px; background: var(--ink-muted);
  }
  .front-brand .name {
    font-weight: 300; font-size: 30px; letter-spacing: 4px;
    color: var(--ink-muted); text-transform: uppercase;
  }

  .back-shape { position: absolute; inset: 0; }

  .holder-name {
    position: absolute; left: 34px; top: 36px;
    font-weight: 300; font-size: 21px; letter-spacing: 2.5px;
    color: var(--ink-light); text-transform: uppercase;
  }
  .contact {
    position: absolute; left: 34px; top: 196px;
    color: var(--ink-light); font-size: 14.5px; line-height: 22px;
  }
  .contact-row { display: flex; align-items: center; gap: 10px; }
  .contact-row svg { width: 12px; height: 12px; flex: none; }
  .address { margin-top: 2px; }

  .back-brand {
    position: absolute; right: 40px; top: 50%;
    transform: translateY(-50%);
    display: flex; flex-direction: column; align-items: center; gap: 14px;
  }
  .back-brand .mark { width: 20px; height: 20px; background: var(--ink-light); }
  .back-brand .name {
    writing-mode: vertical-rl; transform: rotate(180deg);
    font-weight: 300; font-size: 22px; letter-spacing: 3px;
    color: var(--ink-light); text-transform: uppercase;
  }
</style>
</head>
<body>
  <section class="card card-front">
    <div class="front-brand">
      <span class="mark"></span>
      <span class="name">Ferncliff Advisory</span>
    </div>
  </section>

  <section class="card card-back">
    <svg class="back-shape" viewBox="0 0 620 354" preserveAspectRatio="none">
      <path d="M 430 0 Q 330 170 405 354 L 620 354 L 620 0 Z" fill="var(--panel-dark)"/>
    </svg>

    <div class="holder-name">Daniel Whitcombe</div>

    <div class="contact">
      <div class="contact-row">
        <svg viewBox="0 0 12 12"><rect x="0.5" y="2" width="11" height="8" fill="#fff"/><path d="M0.5 2 L6 6.5 L11.5 2" stroke="#0e4479" fill="none"/></svg>
        <span>dan@ferncliffadvisory.com</span>
      </div>
      <div class="contact-row">
        <svg viewBox="0 0 12 12"><circle cx="6" cy="6" r="5.5" fill="#fff"/><path d="M0.5 6 H11.5 M6 0.5 V11.5 M2 3 H10 M2 9 H10" stroke="#0e4479" stroke-width="0.8"/></svg>
        <span>www.ferncliffadvisory.com</span>
      </div>
      <div class="address">2870 North 9th Avenue, Summit<br>Floor, Elm Ridge, Illinois 60531</div>
    </div>

    <div class="back-brand">
      <span class="name">Ferncliff Advisory</span>
      <span class="mark"></span>
    </div>
  </section>
</body>
</html>
```